Need help in designing new business card utilizing our new logo.

BuildMark Solutions works with Construction Business Owners, Managers & IT Professionals to strengthen software usage and increase user productivity.

Our Construction Accounting and Mobile Field Management Software Clients engage with us in the following areas:

New Software Implementations
Software Re-Implementations
Redesigning Software Usage at the User Level
Project Coordination & Management
Continued Software Support

Old tag line:
Careful Planning - Dependable Systems

www.buildmark-solutions.example

Ridge 4 is a product, but not needed for a new business card.

```html
<!DOCTYPE html>
<html lang="en">
<head>
<meta charset="utf-8">
<title>BuildMark Solutions – Business Card</title>
<link rel="stylesheet" href="https://fonts.googleapis.com/css2?family=Roboto:wght@400;700&family=Roboto+Condensed:wght@700&display=swap">
<style>
  :root {
    --navy: #0c1596;
    --paper: #f1f1f2;
    --grey: #a9a9ab;
    --grey-light: #c9c9cb;
    --ink: #222;
    --stage: #e4e4e6;
  }
  * { margin: 0; padding: 0; box-sizing: border-box; }
  html, body { width: 1200px; height: 576px; overflow: hidden; }
  body {
    background: var(--stage);
    font-family: "Roboto", Arial, sans-serif;
    position: relative;
  }
  .card {
    position: absolute;
    top: 138px;
    width: 485px;
    height: 294px;
    border-radius: 12px;
    background: var(--paper);
    overflow: hidden;
  }
  .card-front { left: 82px; }
  .card-back { left: 602px; }

  /* front */
  .front-brand {
    position: absolute;
    top: 52px; left: 0; right: 0;
    display: flex; align-items: center; justify-content: center; gap: 14px;
  }
  .brand-square { width: 36px; height: 36px; background: var(--navy); }
  .brand-name {
    font-weight: 700; color: var(--navy);
    font-size: 32px; letter-spacing: 0.5px;
    white-space: nowrap;
  }
  .services-band {
    position: absolute;
    top: 168px; left: 0; right: 0; height: 80px;
    background: var(--navy);
    color: #fff;
    font-size: 13.5px; line-height: 18.5px;
    text-align: center;
    padding-top: 12px;
    white-space: nowrap;
  }
  .services-band .sep { margin: 0 8px; }
  .front-web {
    position: absolute; top: 262px; left: 0; right: 0;
    display: flex; align-items: center; justify-content: center; gap: 18px;
    font-size: 12px; color: var(--navy);
  }
  .front-web .rule { width: 42px; height: 1px; background: var(--grey); }

  /* back */
  .back-shape { position: absolute; inset: 0; }
  .back-brand {
    position: absolute; top: 96px; left: 0; width: 200px;
    display: flex; flex-direction: column; align-items: center; gap: 10px;
  }
  .back-brand .brand-square { width: 40px; height: 40px; }
  .back-brand .brand-name { font-size: 22px; text-align: center; line-height: 1.15; }
  .contact {
    position: absolute; left: 252px; top: 50px;
    color: #fff;
    white-space: nowrap;
  }
  .contact-name {
    font-family: "Roboto Condensed", "Arial Narrow", sans-serif;
    font-weight: 700; font-size: 22px; line-height: 26px;
  }
  .contact-role { font-size: 12px; margin-top: 2px; }
  .contact-address { font-size: 12px; line-height: 17px; margin-top: 14px; }
  .contact-list { list-style: none; margin-top: 9px; font-size: 12px; line-height: 17px; }
  .contact-list li { display: flex; align-items: center; gap: 9px; }
  .contact-list svg { width: 11px; height: 11px; flex: none; }
  .tagline {
    position: absolute; left: 202px; right: 0; top: 254px; height: 17px;
    background: var(--grey-light);
    color: var(--ink); font-size: 12px; line-height: 17px;
    text-align: center;
    white-space: nowrap;
  }
</style>
</head>
<body>

<section class="card card-front" aria-label="Business card front">
  <div class="front-brand">
    <span class="brand-square" aria-hidden="true"></span>
    <span class="brand-name">BuildMark Solutions</span>
  </div>
  <div class="services-band">
    <p>New Software Implementations<span class="sep">|</span>Software Re-Implementations</p>
    <p>Redesigning Software Usage at the User Level</p>
    <p>Project Coordination &amp; Management<span class="sep">|</span>Continued Software Support</p>
  </div>
  <div class="front-web">
    <span class="rule"></span>
    <span>www.buildmark-solutions.example</span>
    <span class="rule"></span>
  </div>
</section>

<section class="card card-back" aria-label="Business card back">
  <svg class="back-shape" viewBox="0 0 485 294" preserveAspectRatio="none" aria-hidden="true">
    <path d="M180 0 Q200 150 190 294 L485 294 L485 0 Z" fill="var(--grey)"/>
    <path d="M188 0 Q208 150 202 294 L485 294 L485 0 Z" fill="var(--navy)"/>
  </svg>

  <div class="back-brand">
    <span class="brand-square" aria-hidden="true"></span>
    <span class="brand-name">BuildMark<br>Solutions</span>
  </div>

  <div class="contact">
    <h1 class="contact-name">Dana R. Whitfield</h1>
    <p class="contact-role">Owner</p>
    <p class="contact-address">48 Meadow Lane - Suite 112<br>Riverton, NY 12000</p>
    <ul class="contact-list">
      <li><svg viewBox="0 0 12 12" aria-hidden="true"><rect x="3" y="0.5" width="6" height="11" rx="1" fill="none" stroke="#fff" stroke-width="1.2"/><rect x="5" y="9" width="2" height="1" fill="#fff"/></svg>555-014-2298</li>
      <li><svg viewBox="0 0 12 12" aria-hidden="true"><path d="M1 4 Q6 0 11 4 L9.5 5.5 L8 4.5 L4 4.5 L2.5 5.5 Z" fill="#fff"/><rect x="2.5" y="6" width="7" height="5" rx="1" fill="#fff"/></svg>555-010-4400 ext. 100</li>
      <li><svg viewBox="0 0 12 12" aria-hidden="true"><rect x="0.5" y="2.5" width="11" height="7" fill="none" stroke="#fff" stroke-width="1.2"/><path d="M0.5 2.5 L6 7 L11.5 2.5" fill="none" stroke="#fff" stroke-width="1.2"/></svg>dana@buildmark-solutions.example</li>
      <li><svg viewBox="0 0 12 12" aria-hidden="true"><circle cx="6" cy="6" r="5" fill="none" stroke="#fff" stroke-width="1.1"/><ellipse cx="6" cy="6" rx="2.2" ry="5" fill="none" stroke="#fff" stroke-width="1"/><path d="M1 6 H11" stroke="#fff" stroke-width="1"/></svg>www.buildmark-solutions.example</li>
    </ul>
  </div>

  <p class="tagline">Careful Planning - Dependable Systems</p>
</section>

</body>
</html>
```